Responsive Software/Service company website

I need a complete, responsive, company website design (Wordpress).
A short intro to what we do:
Brindlecore is a Danish software company specialized in Zentrova Ledger KEX for SMB clients in Europe.
We deliver POS and ERP systems to retail shops and entertainment business.
Besides this, we offer tight integration to eCommerce solutions.
For eCommerce we have 2 products, both heavily customized for a tight integration.
B2C (Quillora) and B2B
For both eCommerce and KEX solutions we have several sub groups, modules and specifications.
Our target group is existing (looking for eCommerce) and new retailers (looking for POS and eCommerce)
I'm looking for a clean way to promote our products in an easily accessible way.
As well as having a section for more detailed information on each product.
I have uploaded a wire frame suggestion. Please do not take it too literally. You have absolutely creative freedom if you have a better, more creative idea.
See it as an inspiration as to what elements we would like on the site (not necessarily on the front page)
Feel free to use/suggest Stock photos. We are aware that prices of those come on top. We also have pro photographer+studio available if you have any suggestions that requires that.
Updates
Hi all
Target Market(s)
European retailers/shop owners.
Either looking for a POS / ERP system or looking for eCommerce integration to their existing ZL KEX system.
Industry/Entity Type
Entertainment
Requirements
Must have
- The logo I uploaded has to be part of it. Can't be changed.
Same goes for colours
Must be responsive to work on mobile and desktop. Final design PSDs must reflect this and show how it would look on both platforms.
Final PSds must also show examples of any interaction like mouseover, colour changes, image change or dynamics.
Nice to have
- Custom made icons to accompany(replace?) text links are a very big plus.
Custom made icons/logo for each sub product (see wire frame bottom) :
BC Retail
BC Entertainment
BC Ticketing
BC Webshop
etc
for easily distinction would be a big plus too.
The use of "hand drawn" elements mixed with straight, minimalistic design, like here on ArtHarbor, can be used.
Should not have
- This is the existing site I'm looking to change away from:
http://www.brindlecore.example/ (in danish)
Too much info, too cramped, not nice looking and generally not very user friendly imo.

```html
<!DOCTYPE html>
<html lang="en">
<head>
<meta charset="utf-8">
<title>Brindlecore – Mobile Home</title>
<link rel="stylesheet" href="https://fonts.googleapis.com/css2?family=Open+Sans:wdth,wght@75..100,300..800&display=swap">
<style>
  :root {
    --page-bg: #1b1b1b;
    --bar-top: #3b3b3b;
    --bar-bottom: #2b2b2b;
    --brand-bg: #2a2a2a;
    --select-bg: #f1f1f1;
    --select-text: #333333;
    --accent: #3aa6dc;
    --brand-blue: #1f74bd;
    --hero-bg: #e6e5e2;
    --hero-ink: #262626;
    --hero-highlight: #3a9fe6;
    --features-bg: #262626;
    --divider: #1c1c1c;
    --circle: #1e1e1e;
    --title: #ffffff;
    --subtitle: #3497e0;
    --body-text: #e8e8e8;
  }
  * { box-sizing: border-box; margin: 0; padding: 0; }
  html, body {
    width: 1200px; height: 2491px; overflow: hidden;
    background: var(--page-bg);
    font-family: "Open Sans", Arial, sans-serif;
  }
  .site { width: 1200px; height: 2491px; display: flex; flex-direction: column; }

  .menu-bar {
    height: 191px;
    background: linear-gradient(var(--bar-top), var(--bar-bottom));
    border-bottom: 2px solid #222;
    padding: 55px 42px 0;
  }
  .menu-select {
    height: 68px; background: var(--select-bg);
    display: flex; align-items: center; justify-content: space-between;
    padding: 0 37px 0 25px;
    font-size: 35px; color: var(--select-text);
  }
  .menu-toggle {
    width: 53px; height: 53px; background: var(--accent);
    display: flex; align-items: center; justify-content: center;
  }

  .brand-band {
    height: 429px; background: var(--brand-bg);
    border-bottom: 3px solid #202020;
    display: flex; align-items: center; padding: 0 42px 40px;
  }
  .brand-name {
    font-size: 112px; font-weight: 600; letter-spacing: 6px;
    color: var(--brand-blue); line-height: 1;
  }

  .hero {
    position: relative; height: 673px;
    background: radial-gradient(ellipse at 30% 50%, #f4f3f0, var(--hero-bg) 70%, #d8d7d3);
    overflow: hidden;
  }
  .hero-tagline {
    position: absolute; left: 50px; top: 150px; width: 470px;
    text-align: center;
    font-stretch: 75%; font-weight: 700;
    font-size: 48px; line-height: 66px;
    text-transform: uppercase; color: var(--hero-ink);
    text-shadow: 0 0 4px #fff, 0 2px 3px rgba(0,0,0,.35);
    white-space: nowrap;
  }
  .hero-tagline .highlight { color: var(--hero-highlight); }
  .hero-photo {
    position: absolute; right: 40px; bottom: 0; width: 610px; height: 623px;
    background: linear-gradient(180deg, #b9a99a 0%, #6b5d54 30%, #1e1e1e 60%, #111 100%);
    border-radius: 280px 280px 0 0;
    opacity: .9;
  }

  .features {
    flex: 1; background: var(--features-bg);
    display: grid; grid-template-columns: 589px 611px;
  }
  .feature {
    display: flex; flex-direction: column; align-items: center;
    padding-top: 81px; text-align: center;
  }
  .feature + .feature { border-left: 3px solid var(--divider); }
  .feature-icon {
    width: 282px; height: 282px; border-radius: 50%;
    background: var(--circle);
    display: flex; align-items: center; justify-content: center;
  }
  .feature-title {
    margin-top: 82px; font-size: 57px; font-weight: 400; color: var(--title); line-height: 1.2;
  }
  .feature-subtitle {
    margin-top: 0; font-size: 42px; color: var(--subtitle); line-height: 1.3;
  }
  .feature-text {
    margin-top: 40px; font-size: 35px; line-height: 57px; color: var(--body-text);
  }
</style>
</head>
<body>
<div class="site">
  <header class="menu-bar">
    <div class="menu-select">
      <span>Select Menu</span>
      <span class="menu-toggle">
        <svg width="26" height="20" viewBox="0 0 26 20"><path d="M0 0h26L13 20z" fill="#fff"/></svg>
      </span>
    </div>
  </header>

  <div class="brand-band">
    <span class="brand-name">Brindlecore</span>
  </div>

  <section class="hero">
    <p class="hero-tagline">Danish software<br>company specialized<br>in <span class="highlight">Zentrova</span><br><span class="highlight">Ledger KEX</span> for<br>SMB clients in<br>Europe.</p>
    <div class="hero-photo" role="img" aria-label="Photo of two smiling business people in dark suits, arms crossed"></div>
  </section>

  <section class="features">
    <article class="feature">
      <div class="feature-icon">
        <svg width="120" height="130" viewBox="0 0 120 130" aria-hidden="true">
          <path d="M42 8h36l-10 20H52z" fill="#fff"/>
          <rect x="48" y="28" width="24" height="8" rx="3" fill="#fff"/>
          <path d="M50 38h20c30 14 44 44 44 62 0 18-14 26-54 26S6 118 6 100c0-18 14-48 44-62z" fill="#fff"/>
          <text x="60" y="112" text-anchor="middle" font-family="Open Sans, Arial, sans-serif" font-size="60" font-weight="700" fill="#1e1e1e">$</text>
        </svg>
      </div>
      <h2 class="feature-title">Retail</h2>
      <p class="feature-subtitle">Solutions for all industies</p>
      <p class="feature-text">Retail industry gets more<br>and more challenges in<br>recent years. Therefore, it is</p>
    </article>
    <article class="feature">
      <div class="feature-icon">
        <svg width="170" height="120" viewBox="0 0 170 120" aria-hidden="true">
          <path d="M4 10h26l22 66h94l18-50H40" fill="none" stroke="#fff" stroke-width="9" stroke-linejoin="round" stroke-linecap="round"/>
          <path d="M44 26h120l-18 50H60z" fill="#fff"/>
          <g stroke="#1e1e1e" stroke-width="4">
            <line x1="70" y1="30" x2="78" y2="74"/><line x1="92" y1="30" x2="96" y2="74"/>
            <line x1="114" y1="30" x2="114" y2="74"/><line x1="136" y1="30" x2="132" y2="74"/>
            <line x1="50" y1="50" x2="158" y2="50"/>
          </g>
          <circle cx="68" cy="102" r="11" fill="#fff"/>
          <circle cx="134" cy="102" r="11" fill="#fff"/>
        </svg>
      </div>
      <h2 class="feature-title">Webshops</h2>
      <p class="feature-subtitle">E-commerce from KEX</p>
      <p class="feature-text">With our e-commerce<br>solution, BrindleShop B2B,<br>the webshop custom</p>
    </article>
  </section>
</div>
</body>
</html>
```